Visit card

Industry/Entity Type

Health Care

Contact Information for Business Card

O VITALIS SYSTEMS
Odile Brevard - chef de Projet

Requirements
Must have
• 318 Gaston Lemaire Street 59710 BÉTHUNE Tel: 33 (0) 327 481 605 Mobile: 06 42 19 37 64 Web: www.quorvexsystems.example Contact: o.brevard@o-vitalissystems.example
Should not have
• Respect for color

```html
<!DOCTYPE html>
<html lang="fr">
<head>
<meta charset="utf-8">
<title>O VITALIS SYSTEMS – Carte de visite</title>
<link rel="stylesheet" href="https://fonts.googleapis.com/css2?family=Open+Sans:wght@400;600;700&display=swap">
<style>
  :root {
    --page-bg: #e9e7e4;
    --card-white: #fbfbfb;
    --card-white-edge: #ececec;
    --card-dark: #2f2f30;
    --card-dark-deep: #1c1c1d;
    --brand-red: #e3202a;
    --ink: #2e2e2e;
    --ink-soft: #555;
    --rule: #8a8a8a;
  }
  * { box-sizing: border-box; margin: 0; padding: 0; }
  html, body { width: 1200px; height: 1021px; overflow: hidden; }
  body {
    background: var(--page-bg);
    font-family: "Open Sans", sans-serif;
    color: var(--ink);
    position: relative;
  }
  .card {
    position: absolute;
    left: 220px;
    width: 760px;
    height: 434px;
    border-radius: 4px;
    box-shadow: 0 6px 18px rgba(0,0,0,0.18);
  }
  .card-back {
    top: 48px;
    background: radial-gradient(ellipse at 20% 10%, #5a5a5c 0%, var(--card-dark) 45%, var(--card-dark-deep) 100%);
  }
  .card-front {
    top: 538px;
    background: linear-gradient(135deg, var(--card-white) 0%, var(--card-white) 60%, var(--card-white-edge) 100%);
    overflow: hidden;
  }
  .brand {
    position: absolute;
    left: 58px;
    top: 190px;
    display: flex;
    align-items: center;
    gap: 14px;
  }
  .brand-dot {
    width: 50px;
    height: 50px;
    border-radius: 50%;
    background: var(--brand-red);
  }
  .brand-name {
    font-weight: 700;
    font-size: 25px;
    letter-spacing: 0.5px;
    color: var(--ink);
    white-space: nowrap;
  }
  .divider {
    position: absolute;
    left: 382px;
    top: 118px;
    width: 1.5px;
    height: 200px;
    background: var(--rule);
  }
  .contact {
    position: absolute;
    left: 408px;
    top: 120px;
    width: 340px;
  }
  .person-name {
    font-weight: 700;
    font-size: 22px;
    color: var(--brand-red);
    line-height: 1.1;
  }
  .person-role {
    font-size: 16px;
    color: var(--ink-soft);
    margin-bottom: 12px;
  }
  .contact-list { list-style: none; }
  .contact-list li {
    display: flex;
    align-items: flex-start;
    gap: 8px;
    font-size: 15.5px;
    line-height: 1.3;
    margin-bottom: 3px;
  }
  .contact-list svg {
    flex: 0 0 14px;
    width: 14px;
    height: 14px;
    margin-top: 3px;
    fill: none;
    stroke: var(--brand-red);
    stroke-width: 2;
  }
  .contact-list svg.solid { fill: var(--brand-red); stroke: none; }
</style>
</head>
<body>

  <section class="card card-back" role="img" aria-label="Dark card back with embossed repeating brand pattern"></section>

  <section class="card card-front">
    <div class="brand">
      <span class="brand-dot"></span>
      <span class="brand-name">O VITALIS SYSTEMS</span>
    </div>

    <div class="divider"></div>

    <div class="contact">
      <p class="person-name">Odile Brevard</p>
      <p class="person-role">chef de Projet</p>
      <ul class="contact-list">
        <li>
          <svg class="solid" viewBox="0 0 14 14"><path d="M7 0a5 5 0 0 0-5 5c0 3.6 5 9 5 9s5-5.4 5-9a5 5 0 0 0-5-5zm0 7a2 2 0 1 1 0-4 2 2 0 0 1 0 4z"/></svg>
          <span>318 Rue Gaston Lemaire<br>59710 BÉTHUNE</span>
        </li>
        <li>
          <svg class="solid" viewBox="0 0 14 14"><path d="M3 0.5l2.5 3-1.5 1.8c.8 1.8 2.2 3.2 4 4l1.8-1.5 3 2.5-1.6 2.4C6 12.4 1.4 7.8 0.8 2.1z"/></svg>
          <span>+33 (0) 327 481 605</span>
        </li>
        <li>
          <svg viewBox="0 0 14 14"><rect x="3.5" y="1" width="7" height="12" rx="1.2"/></svg>
          <span>06 42 19 37 64</span>
        </li>
        <li>
          <svg viewBox="0 0 14 14"><rect x="1" y="3" width="12" height="8.5"/><path d="M1 3l6 5 6-5"/></svg>
          <span>o.brevard@o-vitalissystems.example</span>
        </li>
        <li>
          <svg viewBox="0 0 14 14" style="stroke-width:1.4"><circle cx="7" cy="7" r="6"/><ellipse cx="7" cy="7" rx="2.6" ry="6"/><path d="M1 7h12"/></svg>
          <span>www.quorvexsystems.example</span>
        </li>
      </ul>
    </div>
  </section>

</body>
</html>
```